Harlow Vale Boxing Gym's Fennick Trim-Up Contest

Harlow Vale Boxing Gym Presents
“The Fennick Trim-Up Challenge”
Win the fight for fitness and take home awesome prizes.
1st Place Tavlo Mini (16gb) (value $299)
2nd Place One-Month All Access Membership (value $199)
3rd Place Harlow Vale Boxing Gym Training Gloves, T-Shirt and Handwraps (value $79)
(fine print)
* Men’s & Women’s Divisions – two sets of prizes.
* Contestants must register between June 10th and June 15th. Entry fee is $25.
* At registration, contestants will be required to weigh-in in a private setting. For the duration of the competition, actual weight will not be posted; only percent gain or loss.
* Results are based on percentage weight loss as measured on September 19th.
Note: Harlow Vale Boxing Gym reserves the right to cancel the competition in a division if there are fewer than 10 contestants in that division. In that event, a full refund will be issued to participants in that division.

ABOUT US:
HVBG is not a traditional health club with rows of cardio equipment, weight-training machines, or overcrowded step-aerobic classes. Nor are we like old-school boxing or martial arts studios which can oftentimes be scary and uninviting.

Our goal is to strike a balance between instruction, conditioning and fun. We offer over 70 classes per week: mostly boxing, but also muay thai, mixed martial arts ("MMA"), and boot camps. All of our instructors have fought professionally or at the amateur level so they're teaching from experience, not what they learned from an online course.

Target Market(s)

Gym members.

Industry/Entity Type

Fitness

Requirements
Must have
• Our logo (attached) converted to blue.

```html
<!DOCTYPE html>
<html lang="en">
<head>
<meta charset="utf-8">
<title>Harlow Vale Boxing Gym – The Fennick Trim-Up Challenge</title>
<link rel="stylesheet" href="https://fonts.googleapis.com/css2?family=Bowlby+One&family=Passion+One:wght@400;700&family=Open+Sans:ital,wght@0,300;0,400;1,400&display=swap">
<style>
  :root{
    --sky:#8fe6f8;
    --sun:#f6f04a;
    --sun-pale:#fbf7a8;
    --cloud:#ffffff;
    --cloud-shade:#dff3f9;
    --green:#3ee63a;
    --red:#f2324c;
    --blue:#2336e2;
    --yellow:#eef53e;
    --white:#ffffff;
    --ink:#3a3a3a;
    --teal:#4cd9ea;
  }
  *{margin:0;padding:0;box-sizing:border-box}
  html,body{width:803px;height:1200px;overflow:hidden;background:var(--white)}
  .poster{position:relative;width:803px;height:1200px;background:var(--white);font-family:"Open Sans",sans-serif}
  .presenter{position:absolute;top:0;left:0;width:100%;height:96px;display:flex;align-items:center;justify-content:center;
    font-family:"Bowlby One",sans-serif;font-size:29px;text-transform:uppercase;color:var(--green);
    text-shadow:1px 2px 2px rgba(0,0,0,.25);letter-spacing:.3px}
  .sky{position:absolute;top:96px;left:0;width:100%;height:430px;background:var(--sky)}
  .sun-art{position:absolute;left:30px;top:12px;width:290px;height:300px;
    background:linear-gradient(160deg,var(--sun-pale),var(--sun))}
  .title{position:absolute;left:330px;top:10px;width:440px;text-align:center;color:var(--red);
    font-family:"Passion One",sans-serif;font-weight:700;line-height:1;text-shadow:1px 2px 2px rgba(0,0,0,.2)}
  .title .t-the{display:block;font-size:92px}
  .title .t-name{display:block;font-size:84px;margin-top:-6px}
  .title .t-thin{display:block;font-family:"Open Sans",sans-serif;font-weight:300;font-size:60px;letter-spacing:-1px;margin-top:6px;text-shadow:none}
  .title .t-challenge{display:block;font-size:88px;margin-top:4px}
  .cloud-art{position:absolute;left:20px;top:335px;width:763px;height:95px;
    background:linear-gradient(180deg,var(--cloud) 40%,var(--cloud-shade))}
  .tagline{position:absolute;left:0;top:366px;width:100%;text-align:center;font-family:"Passion One",sans-serif;
    font-weight:700;font-size:30px;color:var(--blue);letter-spacing:.2px}
  .prizes{position:absolute;top:526px;left:0;width:100%;height:226px;display:flex}
  .prize{flex:1;text-align:center;padding-top:34px;font-family:"Passion One",sans-serif;line-height:1.1}
  .prize--blue{background:var(--blue);color:var(--white)}
  .prize--yellow{background:var(--yellow);color:var(--blue)}
  .prize .place{font-size:40px;font-weight:700;display:block}
  .prize .item-big{font-size:58px;font-weight:700;display:block;margin-top:8px}
  .prize .item{font-size:27px;font-weight:700;display:block;margin-top:10px;line-height:1.18}
  .prize .value{font-size:36px;display:block;margin-top:2px}
  .prize .value-sm{font-size:26px;display:block;margin-top:2px}
  .rules{position:absolute;top:784px;left:118px;width:600px;list-style:none;font-size:19.5px;color:var(--ink);line-height:1.3}
  .rules li{position:relative;padding-left:30px;margin-bottom:14px}
  .rules li svg{position:absolute;left:0;top:4px}
  .note{position:absolute;left:20px;top:1096px;width:370px;font-size:12px;font-style:italic;color:#222;line-height:1.35}
  .brand{position:absolute;left:470px;top:1048px;display:flex;align-items:center;gap:12px;
    font-family:"Passion One",sans-serif;font-weight:700;font-size:54px;color:var(--blue);line-height:.95}
  .brand .mark{width:18px;height:18px;border-radius:50%;background:var(--blue);flex:none}
</style>
</head>
<body>
<main class="poster">
  <header class="presenter">Harlow Vale Boxing Gym Presents</header>

  <section class="sky">
    <div class="sun-art" role="img" aria-label="Illustration of a bright smiling cartoon sun with rays"></div>
    <h1 class="title">
      <span class="t-the">The</span>
      <span class="t-name">Fennick</span>
      <span class="t-thin">TRIM-UP</span>
      <span class="t-challenge">Challenge</span>
    </h1>
    <div class="cloud-art" role="img" aria-label="Illustration of a row of soft white clouds"></div>
    <p class="tagline">Win the fight for fitness and take home awesome prizes!</p>
  </section>

  <section class="prizes">
    <div class="prize prize--blue">
      <span class="place">1st Place</span>
      <span class="item-big">Tavlo Mini</span>
      <span class="value">(value $299)</span>
    </div>
    <div class="prize prize--yellow">
      <span class="place">2nd Place</span>
      <span class="item">One-Month<br>All Access<br>Membership</span>
      <span class="value-sm">(value $199)</span>
    </div>
    <div class="prize prize--blue">
      <span class="place">3rd Place</span>
      <span class="item">Harlow Vale<br>Training Gloves,<br>T-Shirt &amp; Handwraps</span>
      <span class="value-sm">(value $79)</span>
    </div>
  </section>

  <ul class="rules">
    <li><svg width="16" height="16" viewBox="0 0 16 16" aria-hidden="true"><g stroke="var(--teal)" stroke-width="2.4" stroke-linecap="round"><path d="M8 1v14M1 8h14M3 3l10 10M13 3L3 13"/></g></svg>Men’s &amp; Women’s Divisions – two sets of prizes.</li>
    <li><svg width="16" height="16" viewBox="0 0 16 16" aria-hidden="true"><g stroke="var(--teal)" stroke-width="2.4" stroke-linecap="round"><path d="M8 1v14M1 8h14M3 3l10 10M13 3L3 13"/></g></svg>Entry fee is $25.</li>
    <li><svg width="16" height="16" viewBox="0 0 16 16" aria-hidden="true"><g stroke="var(--teal)" stroke-width="2.4" stroke-linecap="round"><path d="M8 1v14M1 8h14M3 3l10 10M13 3L3 13"/></g></svg>Contestants must register between June 10th and June 15th.</li>
    <li><svg width="16" height="16" viewBox="0 0 16 16" aria-hidden="true"><g stroke="var(--teal)" stroke-width="2.4" stroke-linecap="round"><path d="M8 1v14M1 8h14M3 3l10 10M13 3L3 13"/></g></svg>At registration, contestants will be required to weigh-in in a private setting. For the duration of the competition, actual weight will not be posted; only percent gain or loss.</li>
    <li><svg width="16" height="16" viewBox="0 0 16 16" aria-hidden="true"><g stroke="var(--teal)" stroke-width="2.4" stroke-linecap="round"><path d="M8 1v14M1 8h14M3 3l10 10M13 3L3 13"/></g></svg>Results are based on percentage weight loss as measured on September 19th.</li>
  </ul>

  <p class="note">Note: Harlow Vale Boxing Gym reserves the right to cancel the competition in a division if there are fewer than 10 contestants in that division. In that event, a full refund will be issued to participants in that division.</p>

  <div class="brand"><span class="mark"></span><span>Harlow Vale<br>Boxing</span></div>
</main>
</body>
</html>
```